Laser Tattoo Removal Business Cards

We are looking for a professional business card design for a laser tattoo removal business. Ideally looking for a black business card design. The name of the business is Brightline Tattoo Removal. We place our cards at local tattoo shops so we ideally are looking for something trendy/edgy to draw both male and female clientele in.

Target Market(s)

Male/Female ages 18-60

Contact Information for Business Card

black background ideally.. hoping to stay within greys, whites and black

Font styles to use
Serif
Sans Serif

Colors
121212
a9a9a9
5c5c5c
f5f5f5
ffffff
7f7f7f
606060
848484
9d9d9d

Requirements
Must have
• Employee Info:
• Melissa Thornbury
• Chief Executive Offer
• m: 919.537.2846
• w: 919.362.4178
• f: 919.685.3907
• mthornbury@brightlinetattooremoval.example
• Address:
• 4615 Oakmere Pkwy, Suite 210
• Raleigh, NC 27654
• Website:
• www.brightlinetattooremoval.example
Nice to have
• Myabe business name on back or logo on back and employee info on the front

```html
<!DOCTYPE html>
<html lang="en">
<head>
<meta charset="utf-8">
<title>Brightline Tattoo Removal – Business Cards</title>
<link href="https://fonts.googleapis.com/css2?family=Josefin+Sans:wght@400&family=Questrial&family=Montserrat:wght@700&display=swap" rel="stylesheet">
<style>
  :root {
    --ink: #121212;
    --stage: #2b2b2b;
    --paper: #ffffff;
    --paper-soft: #f5f5f5;
    --grey-dark: #5c5c5c;
    --grey-mid: #7f7f7f;
    --grey-light: #a9a9a9;
  }
  * { margin: 0; padding: 0; box-sizing: border-box; }
  html, body { width: 1200px; height: 900px; overflow: hidden; }
  body {
    background: var(--stage);
    font-family: "Questrial", "Century Gothic", sans-serif;
    position: relative;
  }
  .card {
    position: absolute;
    left: 250px;
    width: 700px;
    height: 400px;
    border-radius: 16px;
    overflow: hidden;
  }
  .card--back { top: 35px; background: var(--ink); color: var(--paper); }
  .card--front { top: 465px; background: var(--paper); color: var(--ink); }

  .brand {
    position: absolute;
    left: 0; right: 0;
    text-align: center;
    font-family: "Josefin Sans", sans-serif;
    font-weight: 400;
  }
  .card--back .brand { top: 92px; }
  .card--front .brand { top: 42px; }
  .brand__name {
    display: block;
    font-size: 64px;
    letter-spacing: 6px;
    line-height: 1;
  }
  .brand__line {
    display: flex;
    align-items: center;
    justify-content: center;
    gap: 14px;
    margin-top: 26px;
    font-size: 22px;
    letter-spacing: 5px;
  }
  .brand__line::before, .brand__line::after {
    content: "";
    width: 26px;
    height: 1.5px;
    background: currentColor;
  }

  .web-band {
    position: absolute;
    left: 0; right: 0; bottom: 0;
    height: 62px;
    background: var(--paper);
    color: var(--ink);
    display: flex;
    align-items: center;
    justify-content: center;
    font-family: "Montserrat", sans-serif;
    font-weight: 700;
    font-size: 17px;
    letter-spacing: 3px;
  }

  .person {
    position: absolute;
    right: 392px;
    top: 262px;
    text-align: right;
  }
  .person__name { font-family: "Montserrat", sans-serif; font-weight: 700; font-size: 17px; }
  .person__title { font-size: 15px; color: var(--grey-dark); margin-top: 4px; }

  .divider {
    position: absolute;
    left: 328px;
    top: 222px;
    width: 3px;
    height: 110px;
    background: linear-gradient(to bottom, var(--paper), var(--grey-dark) 55%, var(--paper));
  }

  .contacts {
    position: absolute;
    left: 352px;
    top: 212px;
    list-style: none;
  }
  .contacts li {
    display: flex;
    align-items: center;
    gap: 14px;
    height: 29px;
    font-size: 15px;
    color: var(--grey-dark);
  }
  .contacts svg { width: 18px; height: 18px; fill: var(--ink); flex: none; }

  .address-band {
    position: absolute;
    left: 0; right: 0; bottom: 0;
    height: 56px;
    background: var(--ink);
    color: var(--paper-soft);
    display: flex;
    align-items: center;
    justify-content: center;
    font-size: 16px;
    letter-spacing: 0.5px;
  }
</style>
</head>
<body>

<section class="card card--back" aria-label="Card back">
  <div class="brand">
    <span class="brand__name">BRIGHTLINE</span>
    <span class="brand__line">TATTOO REMOVAL</span>
  </div>
  <div class="web-band">www.brightlinetattooremoval.example</div>
</section>

<section class="card card--front" aria-label="Card front">
  <div class="brand">
    <span class="brand__name">BRIGHTLINE</span>
    <span class="brand__line">TATTOO REMOVAL</span>
  </div>

  <div class="person">
    <p class="person__name">Melissa Thornbury</p>
    <p class="person__title">Chief Executive Officer</p>
  </div>

  <div class="divider"></div>

  <ul class="contacts">
    <li>
      <svg viewBox="0 0 24 24" aria-hidden="true"><path d="M3 8c0-2 2-3 9-3s9 1 9 3v2h-5V8H8v2H3zM7 11h10l3 8H4z"/></svg>
      919.362.4178
    </li>
    <li>
      <svg viewBox="0 0 24 24" aria-hidden="true"><path d="M6.6 10.8a15 15 0 0 0 6.6 6.6l2.2-2.2c.3-.3.7-.4 1-.2 1.1.4 2.3.6 3.6.6.6 0 1 .4 1 1V20c0 .6-.4 1-1 1A17 17 0 0 1 3 4c0-.6.4-1 1-1h3.5c.6 0 1 .4 1 1 0 1.3.2 2.5.6 3.6.1.3 0 .7-.2 1z"/></svg>
      919.537.2846
    </li>
    <li>
      <svg viewBox="0 0 24 24" aria-hidden="true"><path d="M7 3h10v5H7zM4 9h16a1 1 0 0 1 1 1v7h-4v4H7v-4H3v-7a1 1 0 0 1 1-1zm5 6v4h6v-4z"/></svg>
      919.685.3907
    </li>
    <li>
      <svg viewBox="0 0 24 24" aria-hidden="true"><path d="M3 5h18v14H3zm2 2v.5l7 5 7-5V7l-7 5z"/></svg>
      mthornbury@brightlinetattooremoval.example
    </li>
  </ul>

  <div class="address-band">4615 Oakmere Pkwy, Suite 210, Raleigh, NC 27654</div>
</section>

</body>
</html>
```